OrchardLane Kiosk Signage

OrchardLane sell fresh fruit and vegetables online and from road side Kiosks.

We need to adapt the current logo for use as signs that will be displayed on roadside kiosks, please see the attached images to view and understand what the Kiosks look like.
The sign needs to:

1. Capture the attention of drivers and
2. Invite them to stop and purchase fresh fruit and veg
3. Communicate the URL www.OrchardLaneProduce.example.nz
4. Communicate the OrchardLane brand
5. Use current logos and imagery

Solution

The designs must closely reflect the current OrchardLane logo (see files attached) and need to include the website. www.OrchardLaneProduce.example.nz The colour palleted also needs to closely resemble the website.

The designs will be used for laser printed signage on vinyl for two applications

1. Kiosk front width: 2.400m x height: 1.000m (94 inches x 40 inches)
2. Kiosk sides: width 0.400m x height: 1.000m (15 inches x 40 inches)

The region where the kiosk's will display is large open space, green hills and fresh fruit and veg growers (orchards and farms everywhere). The region is well known for horticulture, agriculture, viticulture and farming.

The Kiosk images are attached (P1340537, P1350158, P1350159)
OrchardLane logo (round tree)
OrchardLane logo
Updates

Please note, the OrchardLane kiosk signage brief has been updated. (sorry for the inconvenience, but I think we uploaded an unfinished brief) 

We look forward to your submissions. 

Cheers, OrchardLane 

Target Market(s)

Passers buy - mainly in cars as the signage will be displayed on road side fruit and veg stalls. So the signage will be viewed by the general public, and capture those that are interested in purchasing fresh fruit and veg (direct from the farm or orchard)

Industry/Entity Type

Agriculture

Requirements
Must have
• Must match current logo and reflect the design aspects of the website www.orchardlaneproduce.example.nz
Needs to clearly communicate whats for sale, value and fresh produce
Nice to have
• It would be nice to make the tree component of the logo a feature.

```html
<!DOCTYPE html>
<html lang="en">
<head>
<meta charset="utf-8">
<title>OrchardLane Kiosk Side Sign</title>
<link rel="stylesheet" href="https://fonts.googleapis.com/css2?family=Rubik+Dirt&family=Cinzel:wght@700&family=Roboto:wght@500&display=swap">
<style>
  :root {
    --leaf-green: #6c8957;
    --leaf-green-dark: #3f5a2e;
    --leaf-deep: #24361a;
    --chalk: #f4f4ee;
    --clay: #8e5c50;
    --ink: #2c3526;
  }
  html, body {
    margin: 0;
    padding: 0;
    width: 1200px;
    height: 3200px;
    overflow: hidden;
    background: var(--leaf-green);
  }
  .sign {
    position: relative;
    width: 1200px;
    height: 3200px;
    background: var(--leaf-green);
    overflow: hidden;
  }
  .brand-frame {
    position: absolute;
    left: 80px;
    top: 120px;
    width: 1040px;
    height: 400px;
    box-sizing: border-box;
    padding: 0 60px;
    border: 6px solid rgba(244, 244, 238, 0.55);
    border-radius: 28px;
    display: flex;
    align-items: center;
    justify-content: flex-start;
    overflow: hidden;
  }
  .brand-name {
    font-family: "Rubik Dirt", "Arial Black", sans-serif;
    color: var(--chalk);
    line-height: 0.98;
    white-space: nowrap;
  }
  .brand-frame .brand-name {
    font-size: 150px;
    letter-spacing: 2px;
  }
  .tagline {
    position: absolute;
    left: 0;
    top: 540px;
    width: 1200px;
    margin: 0;
    text-align: center;
    font-family: "Cinzel", Georgia, serif;
    font-weight: 700;
    font-size: 68px;
    letter-spacing: 9px;
    color: var(--clay);
    text-transform: uppercase;
  }
  .headline {
    position: absolute;
    left: 0;
    top: 910px;
    width: 1200px;
    margin: 0;
    text-align: center;
    font-family: "Rubik Dirt", "Arial Black", sans-serif;
    font-weight: 400;
    font-size: 196px;
    line-height: 236px;
    color: var(--chalk);
    white-space: nowrap;
  }
  .produce-photo {
    position: absolute;
    left: 0;
    top: 1840px;
    width: 1200px;
    height: 1360px;
    display: block;
  }
  .web-address {
    position: absolute;
    left: 40px;
    top: 2868px;
    width: 660px;
    height: 84px;
    box-sizing: border-box;
    background: var(--chalk);
    border: 4px solid var(--leaf-deep);
    display: flex;
    align-items: center;
    justify-content: center;
    font-family: "Roboto", Arial, sans-serif;
    font-weight: 500;
    font-size: 31px;
    color: var(--ink);
    white-space: nowrap;
  }
  .brand-seal {
    position: absolute;
    left: 700px;
    top: 2680px;
    width: 456px;
    height: 456px;
    box-sizing: border-box;
    border-radius: 50%;
    background: var(--leaf-green-dark);
    border: 14px solid var(--chalk);
    display: flex;
    align-items: center;
    justify-content: center;
    text-align: center;
    overflow: hidden;
  }
  .brand-seal .brand-name {
    font-size: 72px;
  }
</style>
</head>
<body>
<main class="sign">
  <header class="brand-frame">
    <span class="brand-name">Orchard<br>Lane</span>
  </header>
  <p class="tagline">Produce Delivered</p>

  <h1 class="headline">From the<br>Farm to<br>Your Table</h1>

  <svg class="produce-photo" viewBox="0 0 1200 1360" role="img" aria-label="Photograph of a pile of fresh green spinach leaves">
    <defs>
      <linearGradient id="leafShade" x1="0" y1="0" x2="0" y2="1">
        <stop offset="0" stop-color="#5f8149"/>
        <stop offset="0.35" stop-color="#4a6b37"/>
        <stop offset="1" stop-color="#1f3116"/>
      </linearGradient>
    </defs>
    <path d="M0 180 C 200 40, 420 0, 620 60 C 820 110, 1000 160, 1200 320 L 1200 1360 L 0 1360 Z" fill="url(#leafShade)"/>
  </svg>

  <div class="web-address">www.orchardlaneproduce.example.nz</div>

  <div class="brand-seal">
    <span class="brand-name">Orchard<br>Lane</span>
  </div>
</main>
</body>
</html>
```